Business Card Design Project

We need a business card for a new technology services company. We develop software and implement software packages for our business customers and although we will begin with just one or two service offerings, our service offerings will expand over time. Our name comes from the an author, KL Barrow, and his "idea" was that opportunity should be based on ability and achievement, not on social status.

We would like to see a design that is standard in its size and shape, but stands apart in its dramatic color contrasts. The card should not use too many colors - the colors used in the background should highlight the brilliant blues of the logo (see attachment) to dramatic effect. The background should not be white.

If necessary, you can change the color of the words "KL Barrow", but not the word "Idea".

Card size should be U.S. standard 2 inches by 3.5 inches and provide for 1/8 inch bleed area on each side.

We need a design for both sides of the business card, one side communicating the company logo and contact information, the other side being purely graphical, incorporating the logo but no other information.

Contact Information Required:
Kate Brook
KateBrook@klbarrowvista.com
614-387-2259

Target Market(s)

Business executives

Industry/Entity Type

Software

Requirements
Must have
• It must have the full company logo on one side, and at least the graphic element of the logo on the other. Either that or the full logo on both.
Nice to have
• It would be nice to have a design that could work without needing two different textures. For example, it would be nice if the entire card could be shiny, not just parts of the card.

It would also be nice if texture is something we could add later.
Should not have
• The card should not use the color green.

```html
<!DOCTYPE html>
<html lang="en">
<head>
<meta charset="utf-8">
<title>KL Barrow Vista – Business Card</title>
<link rel="stylesheet" href="https://fonts.googleapis.com/css2?family=Roboto:wght@300&family=Source+Sans+3:wght@400&display=swap">
<style>
  :root {
    --canvas: #ffffff;
    --card-yellow: #ffff66;
    --card-edge: #444444;
    --bar-grey: #999999;
    --bar-edge: #777777;
    --brand-grey: #8c8c8c;
    --accent-cyan: #19c3e6;
    --band-light: #00ffff;
    --band-deep: #0a88c6;
    --contact-text: #ffff66;
  }
  html, body {
    margin: 0;
    padding: 0;
    width: 1200px;
    height: 700px;
    overflow: hidden;
    background: var(--canvas);
  }
  .sheet { display: block; width: 1200px; height: 700px; }
  .card-face { fill: var(--card-yellow); stroke: var(--card-edge); stroke-width: 2; }
  .trim-bar { fill: var(--bar-grey); stroke: var(--bar-edge); stroke-width: 1; }
  .brand-name {
    font-family: "Roboto", sans-serif;
    font-weight: 300;
    fill: var(--brand-grey);
    letter-spacing: -1px;
  }
  .brand-dot { fill: var(--accent-cyan); }
  .contact-line {
    font-family: "Source Sans 3", sans-serif;
    font-weight: 400;
    font-size: 23px;
    fill: var(--contact-text);
  }
  .band-start { stop-color: var(--band-light); }
  .band-end { stop-color: var(--band-deep); }
</style>
</head>
<body>
<svg class="sheet" viewBox="0 0 1200 700" width="1200" height="700" role="img" aria-label="Front and back of the KL Barrow Vista business card">
  <defs>
    <linearGradient id="band-gradient" x1="0" y1="0" x2="1" y2="0">
      <stop offset="0" class="band-start"/>
      <stop offset="1" class="band-end"/>
    </linearGradient>
  </defs>

  <!-- Graphic side -->
  <g class="card card-graphic">
    <rect class="card-face" x="1" y="1" width="539" height="348"/>
    <rect class="trim-bar" x="10" y="16" width="514" height="14"/>
    <rect class="trim-bar" x="12" y="318" width="515" height="14"/>
    <circle class="brand-dot" cx="402" cy="165" r="44"/>
    <text class="brand-name" x="52" y="247" font-size="48">KL Barrow Vista</text>
  </g>

  <!-- Contact side -->
  <g class="card card-contact">
    <rect class="card-face" x="659" y="349" width="540" height="350"/>
    <polygon points="659,552 1199,350 1199,650 659,650" fill="url(#band-gradient)"/>
    <rect class="trim-bar" x="671" y="667" width="516" height="14"/>
    <text class="brand-name" x="685" y="420" font-size="22">KL Barrow Vista</text>
    <circle class="brand-dot" cx="848" cy="410" r="17"/>
    <text class="contact-line" x="1172" y="530" text-anchor="end">Kate Brook</text>
    <text class="contact-line" x="1172" y="565" text-anchor="end">KateBrook@klbarrowvista.com</text>
    <text class="contact-line" x="1172" y="600" text-anchor="end">614-387-2259</text>
  </g>
</svg>
</body>
</html>
```